Suds Haven Laundromat Wordpress Design

We need a Wordpress website design for our laundromat, Suds Haven Atlanta, at www.sudshavenatlanta-example.com. We would like to have 6 pages: Home, About Us, Services, Locations, Reviews and Contact us. We will provide content for the text on each page. What we do: We are a full service laundromat that provides dry cleaning drop off, professional laundry services, wash dry fold and self service laundry to the local community. We would like to use the color scheme from our logo to convey a warm, safe, and bright business that caters to its diverse community.
Updates

I like the structure of this laundromat website: http://www.washtroveusa-example.com/ Using my logo and color scheme in the above referenced website is what. Am looking for. The photos attached to the project with the female model should be used as a primary focus and supplemented by actual photos of the equipment.

Target Market(s)

Our target market is a diverse group of people from Midtown Atlanta - LGBTQ community /Locals/Regulars that have been coming to laundromat for 30 years.

Industry/Entity Type

Laundromat

Coding

Coded - Design and coding required

Number of Pages Required

5+ page

Font styles to use
Sans Serif

Colors
0054AA
0677BA
7BADD7
CADEEF
E8F1F8

Requirements
Must have
• Feature this video on the main page: https://videohost-example.com/xq7Rm2bPz4k

```html
<!DOCTYPE html>
<html lang="en">
<head>
<meta charset="utf-8">
<title>Suds Haven Laundromat</title>
<link href="https://fonts.googleapis.com/css2?family=Roboto:ital,wght@0,400;0,500;0,700;0,900;1,400&family=Great+Vibes&display=swap" rel="stylesheet">
<style>
:root{
  --blue:#0054aa;
  --blue-deep:#084d98;
  --blue-mid:#0677ba;
  --red:#c8121a;
  --red-deep:#b00b10;
  --ink:#222;
  --text:#444;
  --dark:#1c1c1c;
  --black:#0a0a0a;
  --white:#fff;
}
*{box-sizing:border-box;margin:0;padding:0}
html,body{width:1200px;height:2376px;overflow:hidden}
body{position:relative;background:var(--white);font-family:'Roboto',sans-serif;color:var(--text)}
.abs{position:absolute}
.script{font-family:'Great Vibes',cursive;font-weight:400}

/* header */
.topbar{left:323px;top:0;width:877px;height:51px;background:#1a1a1a}
.topbar-cut{left:296px;top:0}
.brand{left:161px;top:18px;font-weight:900;font-size:34px;color:var(--red);letter-spacing:.5px}
.contact-line{top:16px;font-size:12px;color:#eee}
.addr{left:518px}
.phone{left:817px}
.social{top:9px;width:28px;height:28px;border:1.5px solid #ddd;border-radius:50%}
.nav{left:503px;top:51px;width:697px;height:57px;background:var(--blue);border-radius:30px 0 0 0}
.nav ul{list-style:none;display:flex;gap:23px;position:absolute;left:40px;top:21px}
.nav li{color:var(--white);font-size:13px;font-weight:500;text-transform:uppercase}

/* hero */
.hero{left:0;top:78px;width:1200px;height:600px;background:linear-gradient(180deg,#b9d6d2 0%,#c9c4b2 35%,#8f8f8c 70%,#6e6a63 100%)}
.video{left:690px;top:611px;width:350px;height:423px;background:linear-gradient(160deg,#a9b59a 0%,#b7b1a1 45%,#9c9a98 100%)}
.play{left:1008px;top:793px;width:58px;height:58px;border-radius:50%;background:var(--red);border:4px solid var(--white);box-shadow:0 0 0 2px var(--red)}
.play::after{content:"";position:absolute;left:21px;top:15px;border-left:17px solid var(--white);border-top:10px solid transparent;border-bottom:10px solid transparent}

/* welcome */
.welcome-kicker{left:161px;top:697px;font-size:15px;letter-spacing:2px;color:#333}
.welcome-title{left:160px;top:708px;font-size:58px;color:var(--red)}
.welcome-copy{left:160px;top:790px;width:484px;font-size:12.4px;line-height:18.7px}
.welcome-copy p+p{margin-top:25px}
.learn{left:160px;top:985px;font-size:30px;color:#222;display:flex;align-items:center;gap:5px}
.learn .dot{width:15px;height:15px;border-radius:50%;background:var(--red);position:relative;top:2px}
.learn .dot::after{content:"";position:absolute;left:5px;top:4px;border-left:6px solid var(--white);border-top:3.5px solid transparent;border-bottom:3.5px solid transparent}

/* services */
.services-title{left:0;width:1200px;top:1156px;text-align:center;font-size:70px;color:var(--white)}
.svc-icon{width:96px;height:96px;border:3px solid var(--white);border-radius:50%}
.svc-icon svg{position:absolute;left:22px;top:22px}
.svc-name{font-size:20px;font-weight:500;color:var(--white)}
.svc-text{width:300px;font-size:12.2px;line-height:16.5px;color:#dfe9f5}
.more-btn{left:484px;top:1581px;width:231px;height:50px;border-radius:25px;background:var(--red);color:var(--white);font-size:26px;text-align:center;line-height:50px}

/* testimonials */
.t-kicker{left:0;width:1200px;top:1672px;text-align:center;font-size:52px;color:var(--red)}
.t-title{left:0;width:1200px;top:1720px;text-align:center;font-size:57px;font-weight:900;color:var(--ink)}
.quote{top:1810px;width:423px;height:156px;padding:18px 19px;color:var(--white);font-style:italic;font-size:12.8px;line-height:18.7px}
.quote-red{left:161px;background:var(--red-deep)}
.quote-blue{left:615px;background:var(--blue-deep)}
.quote cite{display:block;text-align:right;font-style:normal;font-weight:700;font-size:17px;margin-top:4px}

/* footer */
.footer{left:0;top:2051px;width:1200px;height:279px;background:radial-gradient(ellipse at 40% 40%,#2e2e2e 0%,#1a1a1a 70%)}
.f-kicker{top:2091px;font-size:20px;font-weight:500;color:var(--white)}
.f-head{top:2117px;font-size:29px;font-weight:700;color:var(--white)}
.f-text{left:161px;top:2163px;width:370px;font-size:12.2px;line-height:17.4px;color:#ccc}
.f-links{left:581px;top:2163px;list-style:none;font-size:12.3px;line-height:22.6px;color:#ddd}
.f-contact{left:759px;top:2168px;font-size:12.8px;color:#ddd}
.f-row{display:flex;gap:12px;align-items:flex-start;margin-bottom:14px}
.f-row svg{flex:none;margin-top:1px}
.copyright{left:0;top:2330px;width:1200px;height:46px;background:var(--black);color:#ccc;font-size:11px;text-align:center;line-height:46px}
</style>
</head>
<body>

<!-- hero -->
<div class="abs hero" role="img" aria-label="Photo of a laundromat aisle with rows of washers and a woman in a blue dress"></div>
<svg class="abs" style="left:0;top:600px" width="1200" height="120" viewBox="0 0 1200 120" aria-hidden="true">
  <path d="M0,64 C250,-12 520,-8 720,50 L1040,78 C1110,70 1160,66 1200,62 L1200,120 L0,120Z" fill="#fff"/>
  <path d="M163,62 C300,20 470,18 599,64 C470,32 300,36 163,62Z" fill="#c8121a"/>
</svg>

<!-- header -->
<svg class="abs topbar-cut" width="30" height="78" viewBox="0 0 30 78" aria-hidden="true"><path d="M28,0 L30,0 L30,78 L0,78Z" fill="#1a1a1a"/></svg>
<div class="abs topbar"></div>
<div class="abs" style="left:0;top:0;width:323px;height:78px;background:#fff;clip-path:polygon(0 0,100% 0,91% 100%,0 100%)"></div>
<div class="abs brand">Suds Haven</div>
<div class="abs contact-line addr">&#9679; 2710 Ponce Vista Rd NE., # 112 Atlanta, GA 30399</div>
<div class="abs contact-line phone">&#9742; (404) 555-0142</div>
<div class="abs social" style="left:940px"></div>
<div class="abs social" style="left:974px"></div>
<div class="abs social" style="left:1008px"></div>
<nav class="abs nav">
  <ul><li>Home</li><li>About Us</li><li>Services</li><li>Locations</li><li>Reviews</li><li>Contact Us</li></ul>
</nav>

<!-- welcome -->
<div class="abs welcome-kicker">WELCOME TO</div>
<div class="abs script welcome-title">Suds Haven</div>
<div class="abs welcome-copy">
  <p>Lorem ipsum dolor sit amet, consectetur adipiscing elit. Nam vehicula metus quis nisl facilisis mollis. Curabitur ac blandit tortor, quis tempor nunc. Cras in viverra nulla. Vestibulum ac diam eu nisl pretium viverra sit amet a felis. Morbi ut tellus tincidunt, viverra massa ut, posuere elit.</p>
  <p>Morbi sed tellus ut sapien semper molestie nec at est. Nulla convallis sem ut ante congue fermentum. Sed nec sapien in magna semper consequat. Vivamus at mollis turpis. Donec augue ex, auctor tincidunt tempus sit amet, pellentesque non enim. Lorem ipsum dolor sit amet, consectetur adipiscing elit.</p>
</div>
<div class="abs script learn">Learn More <span class="dot"></span></div>

<div class="abs video" role="img" aria-label="Video preview: woman in a knit beanie listening to earphones in the laundromat"></div>
<div class="abs play" aria-label="Play video"></div>

<!-- services -->
<svg class="abs" style="left:0;top:1060px" width="1200" height="546" viewBox="0 0 1200 546" aria-hidden="true">
  <path d="M0,62 C150,30 290,8 400,12 C560,16 660,68 830,82 C980,92 1100,70 1200,60 L1200,546 L0,546Z" fill="#0a55a6"/>
</svg>
<div class="abs script services-title">What We Do</div>

<div class="abs svc-icon" style="left:164px;top:1277px">
  <svg width="46" height="46" viewBox="0 0 46 46" fill="none" stroke="#fff" stroke-width="3" stroke-linecap="round"><path d="M15,4 q3,4 0,8 M23,4 q3,4 0,8 M31,4 q3,4 0,8"/><rect x="5" y="18" width="36" height="7" rx="3.5"/><rect x="5" y="27" width="36" height="7" rx="3.5"/><rect x="5" y="36" width="36" height="7" rx="3.5"/></svg>
</div>
<div class="abs svc-name" style="left:278px;top:1273px">Dry Cleaning Drop Off</div>
<div class="abs svc-text" style="left:278px;top:1304px">Suspendisse nec risus sem. Nulla ullamcorper mattis lacus non varius. Integer dapibus placerat volutpat. Pellentesque at ipsum quis odio convallis iaculis. Nam fermentum</div>

<div class="abs svc-icon" style="left:626px;top:1277px">
  <svg width="46" height="46" viewBox="0 0 46 46" fill="none" stroke="#fff" stroke-width="2.5"><rect x="8" y="4" width="30" height="38" rx="3"/><line x1="8" y1="12" x2="38" y2="12"/><circle cx="23" cy="27" r="10"/><circle cx="23" cy="27" r="5"/></svg>
</div>
<div class="abs svc-name" style="left:742px;top:1273px">Professional Laundry Services</div>
<div class="abs svc-text" style="left:744px;top:1304px">Suspendisse nec risus sem. Nulla ullamcorper mattis lacus non varius. Integer dapibus placerat volutpat. Pellentesque at ipsum quis odio convallis iaculis. Nam fermentum</div>

<div class="abs svc-icon" style="left:164px;top:1424px">
  <svg width="46" height="46" viewBox="0 0 46 46" fill="none" stroke="#fff" stroke-width="2.5" stroke-linejoin="round"><path d="M20,8 a4,4 0 1 1 4,4 v4 L4,26 h38 L24,16"/><rect x="10" y="26" width="26" height="16" fill="#fff"/></svg>
</div>
<div class="abs svc-name" style="left:279px;top:1427px">Wash Dry Fold</div>
<div class="abs svc-text" style="left:278px;top:1458px">Suspendisse nec risus sem. Nulla ullamcorper mattis lacus non varius. Integer dapibus placerat volutpat. Pellentesque at ipsum quis odio convallis iaculis. Nam fermentum</div>

<div class="abs svc-icon" style="left:626px;top:1424px">
  <svg width="46" height="46" viewBox="0 0 46 46" fill="none" stroke="#fff" stroke-width="2.5"><circle cx="10" cy="9" r="4" fill="#fff"/><path d="M4,30 L6,16 h8 l2,14 M8,30 v12 M12,30 v12"/><rect x="22" y="18" width="20" height="24" rx="2"/><circle cx="32" cy="32" r="6"/></svg>
</div>
<div class="abs svc-name" style="left:743px;top:1427px">Self Service Laundry</div>
<div class="abs svc-text" style="left:743px;top:1458px">Suspendisse nec risus sem. Nulla ullamcorper mattis lacus non varius. Integer dapibus placerat volutpat. Pellentesque at ipsum quis odio convallis iaculis. Nam fermentum</div>

<div class="abs script more-btn">View More Services</div>

<!-- testimonials -->
<div class="abs script t-kicker">Customer</div>
<div class="abs t-title">Testimonials</div>

<div class="abs quote quote-red">“ Suspendisse nec risus sem. Nulla ullamcorper mattis lacus non varius. Integer dapibus placerat volutpat. Pellentesque at ipsum quis odio convallis iaculis. Nam fermentum pellentesque lobortis. Mauris luctus non tellus a aliquam. Donec in arcu ante. Sed vel arcu vel purus”<cite>Maren T.</cite></div>
<svg class="abs" style="left:524px;top:1966px" width="60" height="26" viewBox="0 0 60 26" aria-hidden="true"><path d="M16,0 H60 L0,26Z" fill="#8c0a0e"/></svg>
<div class="abs quote quote-blue">“ Suspendisse nec risus sem. Nulla ullamcorper mattis lacus non varius. Integer dapibus placerat volutpat. Pellentesque at ipsum quis odio convallis iaculis. Nam fermentum pellentesque lobortis. Mauris luctus non tellus a aliquam. Donec in arcu ante. Sed vel arcu vel purus”<cite>Maren T.</cite></div>
<svg class="abs" style="left:977px;top:1966px" width="60" height="26" viewBox="0 0 60 26" aria-hidden="true"><path d="M16,0 H60 L0,26Z" fill="#063a72"/></svg>

<!-- footer -->
<div class="abs footer" role="img" aria-label="Dark faded photo of washing machines"></div>
<div class="abs f-kicker" style="left:161px">About</div>
<div class="abs f-head" style="left:161px">Suds Haven</div>
<div class="abs f-text">Suspendisse nec risus sem. Nulla ullamcorper mattis lacus non varius. Integer dapibus placerat volutpat. Pellentesque at ipsum quis odio convallis iaculis. Nam fermentum pellentesque lobortis. Mauris luctus non tellus a aliquam. Donec in arcu ante. Sed vel arcu vel purus placerat volutpat.</div>

<div class="abs f-kicker" style="left:581px">Quick</div>
<div class="abs f-head" style="left:581px">Links</div>
<ul class="abs f-links">
  <li>› Home</li><li>› About Us</li><li>› Services</li><li>› Locations</li><li>› Reviews</li><li>› Contact us</li>
</ul>

<div class="abs f-kicker" style="left:759px">Contact</div>
<div class="abs f-head" style="left:759px">Details</div>
<div class="abs f-contact">
  <div class="f-row"><svg width="14" height="18" viewBox="0 0 14 18"><path d="M7,0 a7,7 0 0 1 7,7 c0,5 -7,11 -7,11 s-7,-6 -7,-11 a7,7 0 0 1 7,-7z" fill="#ccc"/><circle cx="7" cy="7" r="2.6" fill="#222"/></svg><span>2710 Ponce Vista Rd NE., # 112<br>Atlanta, GA 30399</span></div>
  <div class="f-row"><svg width="16" height="16" viewBox="0 0 16 16"><path d="M3,1 l3,0 l1,4 l-2,1.5 c1,2 2.5,3.5 4.5,4.5 l1.5,-2 l4,1 l0,3 c0,1 -1,2 -2,2 C6,15 1,10 1,3 c0,-1 1,-2 2,-2z" fill="#ccc"/></svg><span>(404) 555-0142</span></div>
  <div class="f-row"><svg width="16" height="12" viewBox="0 0 16 12"><rect width="16" height="12" rx="1" fill="#ccc"/><path d="M0,1 L8,7 L16,1" stroke="#222" stroke-width="1.4" fill="none"/></svg><span>hello@sudshaven-example.com</span></div>
</div>

<div class="abs copyright">Copyright © Suds Haven 2021. All Rights Reserved.</div>

</body>
</html>
```